Brightwell Supports

We need an updated website that captures the comprehensive services and supports we provide to persons with developmental disabilities. We need a website design that educates families about the services we provide. We would also need a website that is user-friendly so that we could periodically update training schedules and ongoing programming.

• Thank you for submitting designs.  A few things I am hoping to see offered in the website:
• Front page highlights the services we offer (host homes, family caregiver, day program, employment program, SLS program, supported apartment program, behavior/clinical program)
• Front page also highlights any new programs we want to make prominent:  family caregiver, future restaurant employment openings, etc...
• Interactive Training Calendar
• Employee Resources page (link to carevo, email login, etc.)
• Uniform provider application for host home providers
• Information on agency - history, goals, etc.
• Contact Information/Location

 

Fun things to include:

• Client Highlights (featuring a client story each month, etc...)
• Employee highlights (featuring a staff member...)
• link to other Brightwell business pages (Brightwell Therapy and Brightwell Restaurant)

```html
<!DOCTYPE html>
<html lang="en">
<head>
<meta charset="utf-8">
<title>Brightwell Supports</title>
<link href="https://fonts.googleapis.com/css2?family=Lato:ital,wght@0,300;0,400;0,700;1,300;1,400&display=swap" rel="stylesheet">
<style>
:root{
  --red:#8c2f31;
  --red-dark:#7a2729;
  --ink:#333333;
  --muted:#666666;
  --charcoal:#3d3d3d;
  --topbar:#4a4a4a;
  --footer:#7b7b7b;
  --footer-dark:#2e2e2e;
  --white:#ffffff;
  --light:#f4f4f4;
}
*{box-sizing:border-box;margin:0;padding:0}
html,body{width:1200px;height:2230px;overflow:hidden}
body{font-family:'Lato',sans-serif;color:var(--ink);background:var(--white);position:relative}
.abs{position:absolute}

/* top bar */
.topbar{left:0;top:0;width:1200px;height:36px;background:var(--topbar);color:#e6e6e6;font-size:11px}
.topbar .social{left:198px;top:10px;display:flex;gap:8px}
.topbar .social span{width:15px;height:15px;border-radius:50%;background:#dcdcdc;display:block}
.topbar .contact{left:560px;top:11px;display:flex;gap:26px;align-items:center}
.topbar .contact span{display:flex;align-items:center;gap:6px}

/* nav */
.nav{left:0;top:36px;width:1200px;height:82px;background:var(--white)}
.brand{left:180px;top:24px;display:flex;align-items:center;gap:8px;font-size:24px;font-weight:700;color:var(--red)}
.brand i{width:14px;height:14px;border-radius:50%;background:var(--red);display:block}
.menu{left:476px;top:0;display:flex;height:82px}
.menu a{display:flex;align-items:center;justify-content:center;text-align:center;padding:0 14px;font-size:10px;font-weight:700;color:var(--red);text-decoration:none;text-transform:uppercase;line-height:1.2;border-right:1px solid #e2e2e2}
.menu a.active{background:var(--red);color:var(--white)}
.dropdown{left:628px;top:118px;width:150px;background:var(--red);z-index:5}
.dropdown div{padding:7px 12px;font-size:9px;font-weight:700;color:var(--white);text-transform:uppercase;border-bottom:1px solid rgba(255,255,255,.25)}

/* hero */
.hero{left:0;top:118px;width:1200px;height:354px;background:linear-gradient(90deg,#8f7a70 0%,#c9b8ad 22%,#e9e6e3 45%,#efeeec 65%,#cfcac6 100%)}
.hero-copy{left:188px;top:106px;width:418px;padding:20px 32px;background:rgba(255,255,255,.45);font-size:25px;line-height:37px;letter-spacing:1.5px;color:var(--red);text-transform:uppercase}
.dots{left:544px;top:427px;display:flex;gap:18px}
.dots span{width:12px;height:12px;border-radius:50%;background:var(--red)}
.dots span.on{background:var(--white);border:2px solid var(--red)}
.hero-rule{left:0;top:472px;width:1200px;height:4px;background:var(--red)}

/* section heading */
.heading{width:1200px;text-align:center;font-size:21px;font-weight:300;letter-spacing:1px;text-transform:uppercase}
.heading::after{content:"";display:block;width:150px;height:2px;margin:8px auto 0;background:currentColor}

/* services */
.service{width:300px;height:140px}
.service .icon{left:0;top:0;width:76px;height:76px;border-radius:50%;background:var(--red)}
.service .label{left:-22px;top:84px;width:120px;text-align:center;font-size:10px;letter-spacing:1px;color:var(--red);text-transform:uppercase;line-height:1.35}
.service p{left:96px;top:-4px;width:150px;font-size:10.5px;line-height:14px;color:var(--muted)}

/* mission */
.mission{left:0;top:888px;width:1200px;height:174px;background:var(--red);color:var(--white)}
.mission p{left:0;top:78px;width:1200px;text-align:center;font-size:15px;font-weight:300;line-height:30px;color:#f2dcdc}

/* team */
.team{left:0;top:1062px;width:1200px;height:528px;background:var(--charcoal);color:var(--white)}
.member{width:300px;top:120px;text-align:center}
.member .photo{width:168px;height:168px;border-radius:50%;margin:0 auto;border:4px solid var(--white);background:radial-gradient(circle at 50% 40%,#d8b9a2,#8a6a58)}
.member h3{margin-top:24px;font-size:15px;font-weight:700;letter-spacing:.5px}
.member .role{font-size:10px;letter-spacing:1px;color:#cfcfcf;text-transform:uppercase;margin-top:2px}
.member p{width:216px;margin:16px auto 0;text-align:left;font-size:10.5px;line-height:16px;color:#d7d7d7}
.member .links{display:flex;justify-content:center;gap:12px;margin-top:24px}
.member .links span{width:22px;height:22px;border-radius:50%;background:var(--white)}

/* testimonial */
.quote{left:0;top:1590px;width:1200px;height:172px;background:var(--red);color:var(--white)}
.quote p{right:270px;top:68px;width:560px;text-align:right;font-size:17px;font-style:italic;font-weight:300;line-height:24px;color:#f2dcdc}
.quote cite{right:270px;top:124px;font-size:13px;font-style:normal;font-weight:700}

/* map */
.map{left:0;top:1762px;width:1200px;height:174px;background:linear-gradient(100deg,#ececec 0%,#e2e2e2 55%,#cfd6dc 75%,#bfc9d2 100%)}

/* customers */
.customers{left:0;top:1936px;width:1200px;height:96px;background:var(--white)}
.customers h4{left:180px;top:38px;font-size:19px;font-weight:300;color:var(--muted)}
.customers .logo{top:40px;width:76px;height:20px;border-radius:10px;background:#d6d6d6}

/* footer */
.footer{left:0;top:2032px;width:1200px;height:178px;background:var(--footer);color:#f0f0f0}
.fcol{top:44px;font-size:9px;line-height:14px}
.fcol h5{font-size:9px;font-weight:700;letter-spacing:1px;text-transform:uppercase;padding-bottom:5px;margin-bottom:10px;border-bottom:1px solid #9a9a9a;width:150px}
.fcol .field{width:160px;height:14px;background:var(--white);margin-top:8px;font-size:8px;color:#999;padding:2px 5px;line-height:10px}
.fcol .btn{width:100px;height:8px;background:var(--red);margin-top:4px}
.bottom{left:0;top:2210px;width:1200px;height:20px;background:var(--footer-dark);color:#cfcfcf;font-size:9px;text-align:center;line-height:20px;letter-spacing:1px;text-transform:uppercase}
</style>
</head>
<body>

<header>
  <div class="abs topbar">
    <div class="abs social"><span></span><span></span><span></span><span></span><span></span></div>
    <div class="abs contact">
      <span>(303) 555-0147</span>
      <span><svg width="10" height="12" viewBox="0 0 10 12"><path d="M2 0h2l1 3-1.5 1a6 6 0 0 0 3 3L8 5.5l2 1v2c0 1-1 2-2 2C4 10 0 6 0 2c0-1 1-2 2-2z" fill="#e6e6e6"/></svg>+1 (303) 555-0162</span>
      <span><svg width="14" height="10" viewBox="0 0 14 10"><rect width="14" height="10" fill="#e6e6e6"/><path d="M0 0l7 6 7-6" stroke="#4a4a4a" fill="none"/></svg>info@brightwellsupports.org</span>
      <span><svg width="11" height="11" viewBox="0 0 11 11"><circle cx="4.5" cy="4.5" r="3.5" stroke="#e6e6e6" stroke-width="1.5" fill="none"/><path d="M7 7l3.5 3.5" stroke="#e6e6e6" stroke-width="1.5"/></svg>SEARCH</span>
    </div>
  </div>

  <nav class="abs nav">
    <div class="abs brand"><i></i>Brightwell Supports</div>
    <div class="abs menu">
      <a href="#">Services</a>
      <a href="#">Become a<br>Provider</a>
      <a href="#" class="active">Programs</a>
      <a href="#">Location</a>
      <a href="#">Community<br>Resources</a>
      <a href="#">Support</a>
      <a href="#">Our Team</a>
    </div>
  </nav>
  <div class="abs dropdown">
    <div>Residential Program</div>
    <div>Day/Employment Program</div>
    <div>SLS Program</div>
    <div>Residential Program</div>
  </div>
</header>

<section class="abs hero" role="img" aria-label="Photo of a caregiver smiling with an elderly woman"></section>
<div class="abs hero-copy">Building Abilities<br>Creating Opportunities<br>Developing Relationships</div>
<div class="abs dots"><span class="on"></span><span></span><span></span><span></span></div>
<div class="abs hero-rule"></div>

<section class="services">
  <h2 class="abs heading" style="left:0;top:492px;color:var(--red)">Services</h2>

  <div class="abs service" style="left:200px;top:584px">
    <svg class="abs icon" viewBox="0 0 76 76"><circle cx="38" cy="38" r="38" fill="#8c2f31"/><path d="M22 38l16-14 16 14h-5v14h-8v-9h-6v9h-8V38z" fill="#fff"/></svg>
    <div class="abs label">Host Home<br>Services</div>
    <p class="abs">Praesent vestibulum aenean nonummy hendrerit mauris. Hasellus porta. Praesent vestibulum aenean nonummy hendrerit mauris. Hasellus porta. Praesent vestibulum aenean nonummy</p>
  </div>
  <div class="abs service" style="left:490px;top:584px">
    <svg class="abs icon" viewBox="0 0 76 76"><circle cx="38" cy="38" r="38" fill="#8c2f31"/><path d="M20 28h4v12h32v10h-4v-5H24v5h-4z M26 34h8v5h-8z M36 34h16a4 4 0 0 1 4 4v1H36z" fill="#fff"/></svg>
    <div class="abs label">Respite<br>Services</div>
    <p class="abs">Praesent vestibulum aenean nonummy hendrerit mauris. Hasellus porta. Praesent vestibulum aenean nonummy hendrerit mauris. Hasellus porta. Praesent vestibulum aenean nonummy</p>
  </div>
  <div class="abs service" style="left:794px;top:584px">
    <svg class="abs icon" viewBox="0 0 76 76"><circle cx="38" cy="38" r="38" fill="#8c2f31"/><circle cx="30" cy="32" r="6" fill="#fff"/><circle cx="46" cy="32" r="6" fill="#fff"/><path d="M19 52a11 11 0 0 1 22 0zM35 52a11 11 0 0 1 22 0z" fill="#fff"/></svg>
    <div class="abs label">Mentor<br>Services</div>
    <p class="abs">Praesent vestibulum aenean nonummy hendrerit mauris. Hasellus porta. Praesent vestibulum aenean nonummy hendrerit mauris. Hasellus porta. Praesent vestibulum aenean nonummy</p>
  </div>

  <div class="abs service" style="left:200px;top:740px">
    <svg class="abs icon" viewBox="0 0 76 76"><circle cx="38" cy="38" r="38" fill="#8c2f31"/><path d="M32 26h12v4h8v22H24V30h8zM35 29v1h6v-1z" fill="#fff"/></svg>
    <div class="abs label">Supported<br>Employment<br>Services</div>
    <p class="abs">Praesent vestibulum aenean nonummy hendrerit mauris. Hasellus porta. Praesent vestibulum aenean nonummy hendrerit mauris. Hasellus porta. Praesent vestibulum aenean nonummy</p>
  </div>
  <div class="abs service" style="left:490px;top:740px">
    <svg class="abs icon" viewBox="0 0 76 76"><circle cx="38" cy="38" r="38" fill="#8c2f31"/><circle cx="35" cy="35" r="11" stroke="#fff" stroke-width="4" fill="none"/><path d="M43 43l10 10" stroke="#fff" stroke-width="5" stroke-linecap="round"/></svg>
    <div class="abs label">Behavioral<br>Services</div>
    <p class="abs">Praesent vestibulum aenean nonummy hendrerit mauris. Hasellus porta. Praesent vestibulum aenean nonummy hendrerit mauris. Hasellus porta. Praesent vestibulum aenean nonummy</p>
  </div>
  <div class="abs service" style="left:794px;top:740px">
    <svg class="abs icon" viewBox="0 0 76 76"><circle cx="38" cy="38" r="38" fill="#8c2f31"/><circle cx="32" cy="28" r="5" fill="#fff"/><path d="M26 36h10l4 8h12v3H38l-3-5v12h-4V42h-5z M42 30h14v10H42z" fill="#fff"/></svg>
    <div class="abs label">Day Program<br>Services</div>
    <p class="abs">Praesent vestibulum aenean nonummy hendrerit mauris. Hasellus porta. Praesent vestibulum aenean nonummy hendrerit mauris. Hasellus porta. Praesent vestibulum aenean nonummy</p>
  </div>
</section>

<section class="abs mission">
  <h2 class="abs heading" style="left:0;top:20px;color:var(--white)">Mission Statement</h2>
  <p class="abs">To promote relationships, attachment, positive boundaries, and resource development<br>to create opportunities and improve the lives of people living with disabilities.</p>
</section>

<section class="abs team">
  <h2 class="abs heading" style="left:0;top:20px;color:var(--white)">Our Team</h2>
  <div class="abs member" style="left:135px">
    <div class="photo" role="img" aria-label="Portrait photo of a team member"></div>
    <h3>CARMEN BRIGHTWELL, LCSW, LAC</h3>
    <div class="role">Executive Director</div>
    <p>Carmen Brightwell has a passion for working with people with disabilities and have made this a significant part of her life. Carmen is a Licensed Clinical Social Worker and Licensed Addictions Counselor, receiving a Masters degree from the University of...</p>
    <div class="links"><span></span><span></span><span></span></div>
  </div>
  <div class="abs member" style="left:425px">
    <div class="photo" role="img" aria-label="Portrait photo of a team member"></div>
    <h3>CARMEN BRIGHTWELL, LCSW, LAC</h3>
    <div class="role">Executive Director</div>
    <p>Carmen Brightwell has a passion for working with people with disabilities and have made this a significant part of her life. Carmen is a Licensed Clinical Social Worker and Licensed Addictions Counselor, receiving a Masters degree from the University of...</p>
    <div class="links"><span></span><span></span><span></span></div>
  </div>
  <div class="abs member" style="left:706px">
    <div class="photo" role="img" aria-label="Portrait photo of a team member"></div>
    <h3>CARMEN BRIGHTWELL, LCSW, LAC</h3>
    <div class="role">Executive Director</div>
    <p>Carmen Brightwell has a passion for working with people with disabilities and have made this a significant part of her life. Carmen is a Licensed Clinical Social Worker and Licensed Addictions Counselor, receiving a Masters degree from the University of...</p>
    <div class="links"><span></span><span></span><span></span></div>
  </div>
</section>

<section class="abs quote">
  <svg class="abs" style="left:216px;top:66px" width="86" height="76" viewBox="0 0 86 76"><path d="M0 0h86v56H30L12 76V56H0z" fill="#a5494b"/><rect x="14" y="16" width="58" height="5" fill="#8c2f31"/><rect x="14" y="28" width="58" height="5" fill="#8c2f31"/><rect x="14" y="40" width="40" height="5" fill="#8c2f31"/></svg>
  <p class="abs">"Praesent vestibulum aenean nonummy hendrerit mauris! Whether you need a motor for a precise medical application."</p>
  <cite class="abs">Daniel Ashford, CEO Corvane Machines</cite>
</section>

<section class="abs map" role="img" aria-label="Street map showing the agency location">
  <svg class="abs" style="left:484px;top:56px" width="56" height="82" viewBox="0 0 56 82"><path d="M28 0a28 28 0 0 1 28 28c0 22-28 54-28 54S0 50 0 28A28 28 0 0 1 28 0z" fill="#8c2f31"/><circle cx="28" cy="27" r="11" fill="#ececec"/></svg>
</section>

<section class="abs customers">
  <h4 class="abs">Our Customers</h4>
  <div class="abs logo" style="left:372px"></div>
  <div class="abs logo" style="left:474px"></div>
  <div class="abs logo" style="left:568px"></div>
  <div class="abs logo" style="left:664px"></div>
  <div class="abs logo" style="left:758px"></div>
  <div class="abs logo" style="left:840px"></div>
  <div class="abs logo" style="left:922px"></div>
</section>

<footer class="abs footer">
  <div class="abs fcol" style="left:205px">
    <h5>About Us</h5>
    <div>420 Linden Street</div>
    <div>Lakewood, CO 80215</div>
    <div>Phone: 303.555.0147</div>
    <div>Fax: 303.555.0162</div>
  </div>
  <div class="abs fcol" style="left:424px">
    <h5>Company</h5>
    <div>About</div><div>Career</div><div>Media Kit</div><div>Contact Us</div>
  </div>
  <div class="abs fcol" style="left:620px">
    <h5>Subscribe to our Newsletter</h5>
    <div>Get news and program updates</div>
    <div>sent to your inbox.</div>
    <div class="field">Email Address</div>
    <div class="btn"></div>
  </div>
  <div class="abs fcol" style="left:870px">
    <h5>Help &amp; Support</h5>
    <div>Terms</div><div>Privacy</div><div>Sign Up</div><div>Login</div>
  </div>
</footer>
<div class="abs bottom">© 2015 All Rights Reserved. Privacy Policy</div>

</body>
</html>
```